Business card for Luxury Portable Restroom Trailer company

We are a Luxury Portable Restroom Trailer Company Called FALCRIDGE HIRES. Based in Orange County California. We provide portable restroom trailers for events, such as, Weddings, Concerts, Charity events, Sporting events, Tournaments, Corporate events, ect. We rent and Sell the Luxury restrooms. Our colors are white, grey, and Orange. As you will see in the logo we uploaded.
There are 2 people in the company so the names and titles will change for the 3 people but card will remain the same. Here is the information for each Person: Dwight Penner CFO 555 318-0476
next Person: Leon Marchetti VP 555 318-0476
Next Person: Owen Marchetti CEO 555 318-0476
Information to include on the card: Luxury Restroom Trailers Rental and Sales. Weddings, Concerts, Charity, Sporting and Corp. Events.

```html
<!DOCTYPE html>
<html lang="en">
<head>
<meta charset="utf-8">
<title>Falcridge Hires – Business Card</title>
<link rel="stylesheet" href="https://fonts.googleapis.com/css2?family=Montserrat:wght@400;600;700;800&display=swap">
<style>
  :root {
    --backdrop: #262626;
    --card: #161616;
    --orange: #f26a21;
    --white: #ffffff;
    --emboss: #0c0c0c;
    --emboss-light: #202020;
  }
  * { box-sizing: border-box; margin: 0; padding: 0; }
  html, body {
    width: 1200px; height: 853px; overflow: hidden;
    background: var(--backdrop);
    font-family: 'Montserrat', sans-serif;
  }
  .stage {
    width: 1200px; height: 853px;
    display: flex; align-items: center; justify-content: center; gap: 40px;
  }
  .card {
    position: relative;
    width: 540px; height: 309px;
    border-radius: 22px;
    background: var(--card);
    box-shadow: 0 14px 30px rgba(0,0,0,.45);
    overflow: hidden;
  }
  /* Front: team contacts */
  .decor-panel {
    position: absolute; right: 0; top: 0; width: 230px; height: 309px;
    background: linear-gradient(135deg, #1c1c1c 0%, #0e0e0e 55%, #121212 100%);
    clip-path: polygon(20% 0, 100% 0, 100% 100%, 0 100%);
    z-index: 0;
  }
  .card-front .brand {
    position: absolute; left: 30px; top: 28px; z-index: 1;
    display: flex; align-items: center; gap: 8px;
    color: var(--orange); font-weight: 800; font-size: 22px; letter-spacing: 1px;
    white-space: nowrap;
  }
  .brand-square { width: 14px; height: 14px; background: var(--orange); flex: none; }
  .contacts { position: absolute; left: 44px; top: 78px; z-index: 1; }
  .contact { margin-bottom: 8px; }
  .contact-name { color: var(--orange); font-weight: 700; font-size: 18px; line-height: 1.15; white-space: nowrap; }
  .contact-title { color: var(--white); font-size: 12px; line-height: 1.35; padding-left: 12px; }
  .contact-phone {
    display: flex; align-items: center; gap: 6px;
    color: var(--white); font-size: 12px; line-height: 1.35; padding-left: 24px;
  }
  .contact-phone svg { width: 12px; height: 12px; fill: var(--orange); flex: none; }
  /* Back: brand statement */
  .card-back .brand-emboss {
    position: absolute; left: 0; right: 0; top: 90px;
    text-align: center;
    color: var(--emboss); font-weight: 800; font-size: 46px; line-height: 1.2; letter-spacing: 3px;
    text-shadow: 0 1px 0 var(--emboss-light);
  }
  .tagline {
    position: absolute; left: 0; right: 0; bottom: 46px;
    text-align: center; color: var(--white); font-size: 13px; line-height: 1.5;
  }
</style>
</head>
<body>
<main class="stage">
  <section class="card card-front">
    <div class="decor-panel" role="img" aria-label="Large dark tone-on-tone brand emblem area"></div>
    <div class="brand"><span class="brand-square"></span>FALCRIDGE HIRES</div>
    <div class="contacts">
      <div class="contact">
        <div class="contact-name">Dwight Penner</div>
        <div class="contact-title">CFO</div>
        <div class="contact-phone"><svg viewBox="0 0 24 24"><path d="M6.6 10.8a15.1 15.1 0 0 0 6.6 6.6l2.2-2.2c.3-.3.7-.4 1-.2 1.1.4 2.3.6 3.6.6.6 0 1 .4 1 1V20c0 .6-.4 1-1 1A17 17 0 0 1 3 4c0-.6.4-1 1-1h3.5c.6 0 1 .4 1 1 0 1.3.2 2.5.6 3.6.1.3 0 .7-.2 1z"/></svg>555 318-0476</div>
      </div>
      <div class="contact">
        <div class="contact-name">Leon Marchetti</div>
        <div class="contact-title">VP</div>
        <div class="contact-phone"><svg viewBox="0 0 24 24"><path d="M6.6 10.8a15.1 15.1 0 0 0 6.6 6.6l2.2-2.2c.3-.3.7-.4 1-.2 1.1.4 2.3.6 3.6.6.6 0 1 .4 1 1V20c0 .6-.4 1-1 1A17 17 0 0 1 3 4c0-.6.4-1 1-1h3.5c.6 0 1 .4 1 1 0 1.3.2 2.5.6 3.6.1.3 0 .7-.2 1z"/></svg>555 318-0476</div>
      </div>
      <div class="contact">
        <div class="contact-name">Owen Marchetti</div>
        <div class="contact-title">CEO</div>
        <div class="contact-phone"><svg viewBox="0 0 24 24"><path d="M6.6 10.8a15.1 15.1 0 0 0 6.6 6.6l2.2-2.2c.3-.3.7-.4 1-.2 1.1.4 2.3.6 3.6.6.6 0 1 .4 1 1V20c0 .6-.4 1-1 1A17 17 0 0 1 3 4c0-.6.4-1 1-1h3.5c.6 0 1 .4 1 1 0 1.3.2 2.5.6 3.6.1.3 0 .7-.2 1z"/></svg>555 318-0476</div>
      </div>
    </div>
  </section>

  <section class="card card-back">
    <div class="brand-emboss">FALCRIDGE<br>HIRES</div>
    <p class="tagline">Luxury Restroom Trailers Rental and Sales.<br>Weddings, Concerts, Charity, Sporting and Corp. Events.</p>
  </section>
</main>
</body>
</html>
```